Figure for presentation on a hybrid research project

We need a figure that shows a series of 6 technical projects feeding into 3 multidisciplinary hybrid projects.
The concept is a ring of 6 technical projects, which could look like a 6 colour swirl (see
https://en.plorvanex.org/wiki/Vector_graphics for an example of a 4 colour swirl.)
The 3 hybrid projects sit in the centre because they rely on input from many of the surrounding technical projects.
I've drawn a rough version in Powerpoint - see attached file uploaded. Note, in my example I couldn't draw the swirling outer ring and the colour selection is poor. The acronym for the overall Centre using the figure is VexORDA, so we will have a mint leaf and turquoise green in the logo, plus also nerves, since we will be researching neural interconnections.
We ABSOLUTELY NEED the final form of the figure to include vector graphics formats (including a form that can be edited in Photoshop) because we may need to change the title of the technical projects or of the hybrid projects at short notice ourselves.

Target Market(s)

Academic: eminent scientists and engineers

Industry/Entity Type

Technical

Font styles to use
Sans Serif

Colors
04a990

Requirements
Must have
• The projects around the ring with all project titles legible; the final figure will be reduced to no more than 8cm x 8cm in the proposal (probably less).
• Only one colour selected, because we have included that colour in the logo that we are having designed. Otherwise, a colour series around the ring that is pleasant, and another compatible colour series for the inter 3 projects.
• We ABSOLUTELY NEED the final form of the figure to include vector graphics formats (including a form that can be edited in Photoshop) because we may need to change the title of the technical projects or of the hybrid projects at short notice ourselves.
Nice to have
• See the figure we uploaded; that's the essence
• HOWEVER VIP: two of the titles around the outer ring have changed slightly.
• Computational Modelling is now Neuronal Modelling and
• Signal Processing is now Non-Invasive Interfaces (note that I've now changed the titles on the uploaded figure)

```html
<!DOCTYPE html>
<html lang="en">
<head>
<meta charset="utf-8">
<title>Hybrid Research Projects Ring</title>
<link rel="stylesheet" href="https://fonts.googleapis.com/css2?family=Arimo:wght@400;700&family=Open+Sans:wght@400;700&display=swap">
<style>
  :root {
    --page-white: #ffffff;
    --backdrop: #85939a;
    --leaf-green: #9bb942;
    --lilac: #936bad;
    --turquoise: #04a990;
    --slate: #546c7a;
    --coral: #f06b63;
    --amber: #f28322;
    --line: #ffffff;
    --hub-light: #f4f6f6;
    --hub-shade: #c9d0d2;
  }
  html, body {
    margin: 0;
    padding: 0;
    width: 1200px;
    height: 834px;
    overflow: hidden;
    background: var(--page-white);
  }
  .figure {
    display: block;
    width: 1200px;
    height: 834px;
  }
  .backdrop { fill: var(--backdrop); }
  .margin-strip { fill: var(--page-white); }
  .petal { stroke: var(--line); stroke-width: 3; stroke-linejoin: round; }
  .petal--01 { fill: var(--leaf-green); }
  .petal--02 { fill: var(--lilac); }
  .petal--03 { fill: var(--turquoise); }
  .petal--04 { fill: var(--slate); }
  .petal--05 { fill: var(--coral); }
  .petal--06 { fill: var(--amber); }
  .ring-outline { fill: none; stroke: var(--line); stroke-width: 3; }
  .project-title {
    font-family: "Arimo", Arial, sans-serif;
    font-size: 31px;
    fill: var(--line);
  }
  .project-number {
    font-family: "Open Sans", Arial, sans-serif;
    font-size: 52px;
    fill: var(--line);
  }
  .hub-base { fill: var(--line); }
  .hub-segment { stroke: var(--line); stroke-width: 2; }
  .hub-segment--wiring { fill: var(--lilac); }
  .hub-segment--perception { fill: var(--amber); }
  .hub-segment--action { fill: var(--turquoise); }
  .hybrid-title {
    font-family: "Arimo", Arial, sans-serif;
    font-size: 37px;
    fill: var(--line);
  }
  .hub-centre { stroke: var(--line); stroke-width: 5; }
  .centre-name {
    font-family: "Arimo", Arial, sans-serif;
    font-weight: 700;
    font-size: 33px;
    fill: var(--turquoise);
  }
</style>
</head>
<body>
<svg class="figure" viewBox="0 0 1439 1000" xmlns="http://www.w3.org/2000/svg" aria-label="Six technical projects in a swirl ring around three hybrid projects">
  <defs>
    <radialGradient id="hub-centre-fill" cx="0.45" cy="0.35" r="0.7">
      <stop offset="0" stop-color="var(--hub-light)"/>
      <stop offset="1" stop-color="var(--hub-shade)"/>
    </radialGradient>
    <filter id="hub-shadow" x="-30%" y="-30%" width="160%" height="160%">
      <feDropShadow dx="0" dy="4" stdDeviation="9" flood-color="#000" flood-opacity="0.45"/>
    </filter>
    <path id="arc-wiring" d="M 707 506 A 115 115 0 0 1 808 361"/>
    <path id="arc-perception" d="M 850 350 A 128 128 0 0 1 940 520"/>
  </defs>

  <rect class="backdrop" x="0" y="0" width="1439" height="1000"/>
  <rect class="margin-strip" x="0" y="0" width="239" height="1000"/>

  <g class="swirl-ring">
    <path class="petal petal--01" d="M 690 358 C 560 410, 430 450, 415 540 A 405 405 0 0 1 548 162 C 640 150, 760 240, 860 300 L 818 476 Z"/>
    <path class="petal petal--02" d="M 860 300 C 760 240, 640 150, 548 162 A 405 405 0 0 1 945 92 C 1010 150, 985 330, 978 440 L 818 476 Z"/>
    <path class="petal petal--03" d="M 978 440 C 985 330, 1010 150, 945 92 A 405 405 0 0 1 1218 420 C 1230 480, 1050 540, 935 598 L 818 476 Z"/>
    <path class="petal petal--04" d="M 935 598 C 1050 540, 1230 480, 1218 420 A 405 405 0 0 1 1085 780 C 1010 810, 880 720, 775 632 L 818 476 Z"/>
    <path class="petal petal--05" d="M 775 632 C 880 720, 1010 810, 1085 780 A 405 405 0 0 1 690 855 C 610 820, 640 640, 660 555 L 818 476 Z"/>
    <path class="petal petal--06" d="M 660 555 C 640 640, 610 820, 690 855 A 405 405 0 0 1 415 540 C 430 450, 560 410, 690 358 L 818 476 Z"/>
    <circle class="ring-outline" cx="818" cy="476" r="405"/>
  </g>

  <g class="technical-projects">
    <text class="project-title" x="705" y="180">Living electrode</text>
    <text class="project-number" x="678" y="287">01</text>
    <text class="project-title" x="490" y="297">Signal</text>
    <text class="project-title" x="490" y="338">processing</text>
    <text class="project-number" x="902" y="315">02</text>
    <text class="project-number" x="1047" y="315">03</text>
    <text class="project-title" x="987" y="400">Gene regulated</text>
    <text class="project-title" x="1037" y="438">interfaces</text>
    <text class="project-number" x="1120" y="565">04</text>
    <text class="project-title" x="892" y="659">Electro-modulated</text>
    <text class="project-title" x="900" y="700">interfaces</text>
    <text class="project-number" x="667" y="690">05</text>
    <text class="project-title" x="790" y="793">Optrode</text>
    <text class="project-title" x="790" y="834">interfaces</text>
    <text class="project-number" x="542" y="720">06</text>
    <text class="project-title" x="438" y="541">Computational</text>
    <text class="project-title" x="438" y="582">modelling</text>
  </g>

  <g class="hybrid-hub">
    <circle class="hub-base" cx="818" cy="476" r="167" filter="url(#hub-shadow)"/>
    <path class="hub-segment hub-segment--wiring" d="M 679.4 556 A 160 160 0 0 1 818 316 L 818 406 A 70 70 0 0 0 757.4 511 Z"/>
    <path class="hub-segment hub-segment--perception" d="M 818 316 A 160 160 0 0 1 956.6 556 L 878.6 511 A 70 70 0 0 0 818 406 Z"/>
    <path class="hub-segment hub-segment--action" d="M 956.6 556 A 160 160 0 0 1 679.4 556 L 757.4 511 A 70 70 0 0 0 878.6 511 Z"/>
    <circle class="hub-segment hub-segment--wiring" cx="827" cy="356" r="12"/>
    <circle class="hub-segment hub-segment--perception" cx="912" cy="520" r="12"/>
    <circle class="hub-segment hub-segment--action" cx="712" cy="518" r="12"/>

    <text class="hybrid-title"><textPath href="#arc-wiring">Brain wiring</textPath></text>
    <text class="hybrid-title"><textPath href="#arc-perception">Perception</textPath></text>
    <text class="hybrid-title" x="805" y="593" text-anchor="middle">Action</text>

    <circle class="hub-centre" cx="818" cy="476" r="66" fill="url(#hub-centre-fill)" filter="url(#hub-shadow)"/>
    <text class="centre-name" x="818" y="488" text-anchor="middle">LOGO</text>
  </g>
</svg>
</body>
</html>
```